Strategic Objective - Internal

Take text supplied in a word document and make a stylish, professional document using elements of our brand .This is an internal document for presentation to our small team . Have attached an example document - please do not copy this - this is just to give you the concept. I would like to be able to edit the text in the document you supply back to me also (In word or photoshop)

Our website is www.brolgatrade.com.au

Have attached out logo
Thank you

Target Market(s)

Our staff

Industry/Entity Type

Mining, Earthmoving

Requirements
Must have
• Professional, stylish presentation
Nice to have
• Our market includes Australia, Papua New Guinea and teh South Pacific - any graphic that supports this. We are an importer and exporter - any graphics that support this.

```html
<!DOCTYPE html>
<html lang="en">
<head>
<meta charset="utf-8">
<title>Strategic Objective – Cover</title>
<link rel="stylesheet" href="https://fonts.googleapis.com/css2?family=Archivo:wght@400;600;700;800&display=swap">
<style>
  :root {
    --page-bg: #e9e8e4;
    --stone-light: #e2e2e0;
    --stone-mid: #b4b4b1;
    --stone-dark: #7c7d7b;
    --brand-blue-bright: #1a5be0;
    --brand-blue: #0d47c4;
    --brand-blue-deep: #0a348f;
    --brand-blue-night: #061f60;
    --accent-lime: #b8d633;
    --title-white: #eef1f7;
  }
  * { margin: 0; padding: 0; box-sizing: border-box; }
  html, body {
    width: 1200px;
    height: 960px;
    overflow: hidden;
    background: var(--page-bg);
    font-family: "Archivo", Arial, sans-serif;
  }
  .canvas {
    width: 1200px;
    height: 960px;
    display: flex;
    align-items: center;
    justify-content: center;
  }
  .cover {
    position: relative;
    width: 630px;
    height: 890px;
    overflow: hidden;
    box-shadow: 0 12px 36px rgba(0,0,0,0.18);
  }
  .cover-photo {
    position: absolute;
    inset: 0;
    background:
      radial-gradient(ellipse 40% 30% at 90% 75%, var(--stone-light) 0%, transparent 70%),
      radial-gradient(ellipse 35% 25% at 12% 90%, var(--stone-dark) 0%, transparent 75%),
      radial-gradient(ellipse 45% 30% at 30% 8%, var(--stone-light) 0%, transparent 70%),
      radial-gradient(ellipse 30% 40% at 95% 30%, var(--stone-dark) 0%, transparent 75%),
      linear-gradient(160deg, var(--stone-mid) 0%, var(--stone-light) 50%, var(--stone-mid) 100%);
  }
  .feature-panel {
    position: absolute;
    left: 50px;
    top: 70px;
    width: 470px;
    height: 760px;
    border-radius: 22px;
    overflow: hidden;
  }
  .feature-photo {
    position: absolute;
    inset: 0;
    background:
      radial-gradient(ellipse 45% 30% at 72% 58%, rgba(60,110,230,0.55) 0%, transparent 70%),
      radial-gradient(ellipse 40% 22% at 30% 70%, rgba(5,25,90,0.65) 0%, transparent 75%),
      radial-gradient(ellipse 50% 25% at 40% 30%, rgba(40,95,220,0.5) 0%, transparent 70%),
      radial-gradient(ellipse 35% 30% at 85% 25%, rgba(6,31,96,0.55) 0%, transparent 75%),
      radial-gradient(ellipse 40% 20% at 55% 45%, rgba(4,22,80,0.45) 0%, transparent 75%),
      radial-gradient(ellipse 30% 18% at 20% 50%, rgba(50,100,225,0.45) 0%, transparent 70%),
      linear-gradient(170deg, var(--brand-blue-bright) 0%, var(--brand-blue) 40%, var(--brand-blue-deep) 75%, var(--brand-blue-night) 100%);
  }
  .brand-mark {
    position: absolute;
    left: 34px;
    top: 38px;
    display: flex;
    align-items: center;
    gap: 10px;
  }
  .brand-dot {
    width: 16px;
    height: 16px;
    border-radius: 50%;
    background: var(--title-white);
  }
  .brand-name {
    font-weight: 700;
    font-size: 17px;
    letter-spacing: 0.5px;
    color: var(--title-white);
  }
  .title-block {
    position: absolute;
    left: 34px;
    bottom: 46px;
  }
  .title-rule {
    width: 110px;
    height: 2px;
    background: var(--accent-lime);
    margin-bottom: 20px;
  }
  .doc-title {
    font-weight: 700;
    font-size: 58px;
    line-height: 1.02;
    letter-spacing: -0.5px;
    color: var(--title-white);
  }
</style>
</head>
<body>
  <main class="canvas">
    <article class="cover">
      <div class="cover-photo" role="img" aria-label="Black and white photograph of a mining excavator bucket and rocky ground"></div>
      <section class="feature-panel">
        <div class="feature-photo" role="img" aria-label="Blue-tinted close-up photograph of an excavator bucket digging into earth"></div>
        <div class="brand-mark">
          <span class="brand-dot"></span>
          <span class="brand-name">BROLGATRADE</span>
        </div>
        <div class="title-block">
          <div class="title-rule"></div>
          <h1 class="doc-title">Strategic<br>Objective</h1>
        </div>
      </section>
    </article>
  </main>
</body>
</html>
```